Real Estate investment company needs billboard designs

This is our website: https://brightlanepropertygroup.com/
We are looking for some billboard concepts that uses our CEO in the design. I have attached some images and 1 billboard design that someone in our industry uses, but we don't want it exactly like his.

Industry/Entity Type

real estate

Colors

Designer to choose colors to be used in the design.

Requirements
Must have
• Company colors from websiute

```html
<!DOCTYPE html>
<html lang="en">
<head>
<meta charset="utf-8">
<title>Bright Lane Property Group – Cash Offer Billboard</title>
<link rel="stylesheet" href="https://fonts.googleapis.com/css2?family=Poppins:wght@300;400;700;800&family=Montserrat:wght@300;800;900&display=swap">
<style>
  :root {
    --stage: #7a7a7a;
    --paper: #ffffff;
    --navy: #1d1c45;
    --navy-deep: #17163a;
    --red: #f0141a;
    --red-bright: #ff1a1a;
    --white: #ffffff;
    --dusk-top: #4b4a82;
    --dusk-low: #23224d;
    --shirt: #2c2c2e;
    --bill: #b9c4ae;
  }
  * { margin: 0; padding: 0; box-sizing: border-box; }
  html, body { width: 1026px; height: 1200px; overflow: hidden; background: var(--stage); }
  .billboard {
    position: absolute; left: 23px; top: 377px; width: 980px; height: 445px;
    background: var(--paper); overflow: hidden;
    box-shadow: 6px 10px 18px rgba(0,0,0,.45);
  }
  .headline-panel {
    position: absolute; left: 42px; top: 38px; width: 896px; height: 265px;
    background: var(--navy); border-radius: 14px 14px 0 0; overflow: hidden;
  }
  .property-photo {
    position: absolute; right: 0; top: 0; width: 360px; height: 265px;
    background: linear-gradient(90deg, var(--navy) 0%, rgba(29,28,69,0) 30%),
                linear-gradient(180deg, var(--dusk-top) 0%, #5a4a70 45%, var(--dusk-low) 100%);
  }
  .contact-band {
    position: absolute; left: 0; top: 306px; width: 980px; height: 139px;
    background: linear-gradient(90deg, var(--red) 0%, var(--red-bright) 100%);
  }
  .ceo-photo {
    position: absolute; left: 724px; top: 84px; width: 256px; height: 361px;
    background: linear-gradient(180deg, #8a7a70 0%, #5e5450 28%, var(--shirt) 40%, #1e1e20 100%);
    border-radius: 110px 110px 0 0;
  }
  .bill {
    position: absolute; width: 78px; height: 34px; background: var(--bill);
    border-radius: 3px; opacity: .95;
  }
  .bill-left { left: -6px; top: 80px; transform: rotate(28deg); }
  .bill-top { left: 898px; top: 4px; transform: rotate(50deg); width: 60px; height: 26px; }
  .bill-mid { left: 585px; top: 220px; transform: rotate(-55deg); }
  .headline {
    position: absolute; left: 80px; font-family: "Montserrat", sans-serif;
    font-weight: 900; font-size: 82px; line-height: 1; letter-spacing: -1px;
  }
  .headline-cash { top: 94px; color: var(--red); }
  .headline-offer { top: 186px; color: var(--white); }
  .timing-box {
    position: absolute; left: 391px; top: 86px; width: 206px; height: 176px;
    border: 1.5px dashed rgba(255,255,255,.8); border-right: none; border-radius: 8px 0 0 0;
    background: rgba(255,255,255,.03);
  }
  .timing {
    position: absolute; left: 400px; font-family: "Montserrat", sans-serif; line-height: 1;
  }
  .timing-on { top: 100px; font-weight: 300; font-size: 56px; color: var(--white); }
  .timing-same { top: 152px; font-weight: 900; font-size: 55px; color: var(--red); letter-spacing: -1px; }
  .timing-day { top: 202px; font-weight: 900; font-size: 55px; color: var(--red); letter-spacing: -1px; }
  .company-name {
    position: absolute; left: 40px; top: 340px; width: 200px;
    font-family: "Poppins", sans-serif; font-weight: 800; font-size: 26px;
    line-height: 1.02; color: var(--navy); text-transform: uppercase;
  }
  .phone {
    position: absolute; left: 280px; top: 330px; display: flex; align-items: center; gap: 8px;
    font-family: "Poppins", sans-serif; font-weight: 800; font-size: 46px;
    line-height: 1; color: var(--white); letter-spacing: .5px;
  }
  .phone svg { width: 36px; height: 36px; }
  .website {
    position: absolute; left: 282px; top: 386px;
    font-family: "Poppins", sans-serif; font-weight: 700; font-size: 20.5px; color: var(--white);
  }
</style>
</head>
<body>
  <section class="billboard">
    <div class="headline-panel">
      <div class="property-photo" role="img" aria-label="Modern apartment building at dusk with lit windows"></div>
    </div>
    <div class="contact-band"></div>

    <div class="headline headline-cash">CA$H</div>
    <div class="headline headline-offer">OFFER</div>

    <div class="timing-box"></div>
    <div class="timing timing-on">ON</div>
    <div class="timing timing-same">SAME</div>
    <div class="timing timing-day">DAY</div>

    <div class="company-name">Bright Lane<br>Property Group</div>

    <div class="phone">
      <svg viewBox="0 0 36 36" aria-hidden="true">
        <circle cx="18" cy="18" r="17" fill="#1d1c45"/>
        <path d="M12.5 9.5c.8-.5 1.8-.3 2.3.5l1.8 3c.4.7.3 1.6-.3 2.1l-1.3 1.1c.9 2 2.5 3.7 4.5 4.6l1.1-1.3c.5-.6 1.4-.8 2.1-.3l3 1.8c.8.5 1 1.5.5 2.3l-1 1.6c-.7 1.1-2 1.6-3.3 1.3-5.2-1.3-9.3-5.4-10.6-10.6-.3-1.3.2-2.6 1.3-3.3z" fill="#ffffff"/>
      </svg>
      <span>555-014-2290</span>
    </div>
    <div class="website">www.brightlanepropertygroup.com</div>

    <div class="ceo-photo" role="img" aria-label="Company CEO in dark polo shirt, arms crossed"></div>

    <div class="bill bill-left" role="img" aria-label="Flying dollar bill"></div>
    <div class="bill bill-top" role="img" aria-label="Flying dollar bill"></div>
    <div class="bill bill-mid" role="img" aria-label="Flying dollar bill"></div>
  </section>
</body>
</html>
```